Website for Excavator and Earthworks Company

We require a modern, sleek and practical website for our newly created earthworks/excavator business in Perth, Western Australia called Bluegum Ridge Earthworks.

The website should have a modern, cutting edge feel but only needs to be relatively simplistic in it's layout and eventual functionality.

Some pages it should have would be Home, About, Projects and Contact Us.

```html
<!DOCTYPE html>
<html lang="en">
<head>
<meta charset="utf-8">
<title>Bluegum Ridge Earthworks</title>
<link href="https://fonts.googleapis.com/css2?family=Big+Shoulders+Display:wght@700;800;900&family=Plus+Jakarta+Sans:wght@400;500;600;700&display=swap" rel="stylesheet">
<style>
:root{
  --lime:#d4dc00;
  --ink:#111111;
  --black:#0d0d0d;
  --white:#ffffff;
  --text:#444444;
  --muted:#9a9a9a;
  --line:#2a2a2a;
}
*{margin:0;padding:0;box-sizing:border-box}
html,body{width:1200px;height:4118px;overflow:hidden}
body{position:relative;background:var(--white);font-family:"Plus Jakarta Sans",sans-serif;color:var(--text)}
.abs{position:absolute}
.display{font-family:"Big Shoulders Display",sans-serif;font-weight:800;text-transform:uppercase;color:var(--ink);line-height:1}
.btn{position:absolute;display:flex;align-items:center;justify-content:center;background:var(--lime);color:var(--ink);font-size:12px;font-weight:600}
.btn-ghost{background:transparent;border:1.5px solid var(--white);color:var(--white)}
.label{font-family:"Big Shoulders Display",sans-serif;font-weight:700;color:var(--lime);font-size:16px;text-transform:uppercase}
.photo{position:absolute}

/* top bar */
.topbar{position:absolute;left:0;top:0;width:1200px;height:29px;background:var(--black);color:var(--white);font-size:11px}
.topbar span{position:absolute;top:8px;display:flex;align-items:center;gap:6px}
.topbar .sep{position:absolute;top:6px;width:1px;height:17px;background:#444}

/* header */
.header{position:absolute;left:0;top:29px;width:1200px;height:78px;background:var(--white)}
.brand{position:absolute;left:75px;top:24px;display:flex;align-items:center;gap:10px;font-weight:700;font-size:18px;color:var(--ink)}
.brand i{display:block;width:26px;height:26px;background:var(--lime)}
.nav{position:absolute;left:666px;top:33px;display:flex;gap:18px;font-size:12px;color:var(--ink)}
.nav b{font-weight:700}
.nav em{font-style:normal;color:#999}

/* hero */
.hero{position:absolute;left:0;top:107px;width:1125px;height:615px;background:linear-gradient(180deg,#4a5a70 0%,#c9642a 38%,#8a4a26 62%,#3c2a1c 100%)}
.hero-side{position:absolute;left:1125px;top:107px;width:75px;height:615px;background:var(--black)}
.hero h1{position:absolute;left:77px;top:248px;font-size:72px;color:var(--white);line-height:0.98}
.outline-lime{color:transparent;-webkit-text-stroke:1.5px var(--lime)}
.hero p{position:absolute;left:77px;top:470px;color:var(--white);font-size:12px}
.dots{position:absolute;left:879px;top:680px;display:flex;gap:4px}
.dots i{display:block;width:58px;height:3px;background:rgba(255,255,255,.4)}
.dots i.on{background:var(--lime)}

/* marquee */
.ticker{position:absolute;left:0;top:722px;width:1200px;height:48px;background:var(--lime);overflow:hidden;white-space:nowrap}
.ticker div{position:absolute;left:-14px;top:14px;font-family:"Big Shoulders Display",sans-serif;font-weight:800;font-size:20px;color:var(--ink);letter-spacing:.2px}
.ticker em{font-style:normal;margin:0 22px}

.outline-band{position:absolute;left:0;top:1396px;width:1200px;height:56px;overflow:hidden;white-space:nowrap}
.outline-band div{position:absolute;left:-10px;top:0;display:flex;align-items:center;gap:20px;font-family:"Big Shoulders Display",sans-serif;font-weight:800;font-size:48px;color:transparent;-webkit-text-stroke:1.2px #8a8a8a}
.outline-band i{display:block;width:34px;height:34px;background:var(--lime)}

.body-copy{font-size:12.5px;line-height:1.55;color:#555}

/* services */
.services{position:absolute;left:0;top:1552px;width:1200px;height:546px;background:var(--black)}
.services .vline{position:absolute;top:0;width:1px;height:546px;background:#1c1c1c}
.arrow-btn{position:absolute;width:43px;height:38px;display:flex;align-items:center;justify-content:center}
.card{position:absolute;top:1777px;width:334px;height:380px}
.card h3{position:absolute;left:30px;bottom:24px;font-family:"Big Shoulders Display",sans-serif;font-weight:800;font-size:22px;color:var(--white);text-transform:uppercase}

/* list */
.ticks{list-style:none;font-size:12px;color:#555}
.ticks li{display:flex;align-items:center;gap:8px;margin-bottom:8.5px}
.ticks li::before{content:"";width:6px;height:6px;background:var(--lime)}

/* projects */
.tile{position:absolute;width:230px;height:196px}

/* cta */
.cta{position:absolute;left:0;top:3595px;width:1200px;height:149px;background:var(--lime)}

/* footer */
.footer{position:absolute;left:0;top:3744px;width:1200px;height:374px;background:var(--black);color:var(--white)}
.foot-h{position:absolute;top:88px;font-family:"Big Shoulders Display",sans-serif;font-weight:700;font-size:19px;text-transform:uppercase;padding-left:10px;border-left:3px solid var(--lime);line-height:1}
.foot-list{position:absolute;list-style:none;font-size:11.5px;line-height:24px}
.foot-list li{display:flex;align-items:flex-start;gap:10px}
.soc{display:block;width:22px;height:22px;border-radius:50%;background:#2a2a2a}
</style>
</head>
<body>

<!-- top bar -->
<div class="topbar">
  <span style="left:78px"><svg width="10" height="10" viewBox="0 0 24 24"><path fill="#d4dc00" d="M6.6 10.8a15 15 0 0 0 6.6 6.6l2.2-2.2a1 1 0 0 1 1-.25 11.4 11.4 0 0 0 3.6.57 1 1 0 0 1 1 1V20a1 1 0 0 1-1 1A17 17 0 0 1 3 4a1 1 0 0 1 1-1h3.5a1 1 0 0 1 1 1c0 1.25.2 2.45.57 3.57a1 1 0 0 1-.25 1z"/></svg>123 ( 456 ) 7890</span>
  <i class="sep" style="left:222px"></i>
  <span style="left:272px"><svg width="11" height="9" viewBox="0 0 24 18"><rect width="24" height="18" rx="2" fill="#d4dc00"/><path d="M1 2l11 8 11-8" stroke="#0d0d0d" stroke-width="2" fill="none"/></svg>info@bluegumridgeearthworks.com.au</span>
  <i class="sep" style="left:512px"></i>
  <span style="left:580px"><svg width="9" height="11" viewBox="0 0 18 24"><path fill="#d4dc00" d="M9 0a9 9 0 0 0-9 9c0 6.8 9 15 9 15s9-8.2 9-15a9 9 0 0 0-9-9zm0 12.5A3.5 3.5 0 1 1 9 5.5a3.5 3.5 0 0 1 0 7z"/></svg>Perth, Western Australia (Servicing Perth &amp; Surrounding Areas)</span>
</div>

<!-- header -->
<header class="header">
  <div class="brand"><i></i>Bluegum Ridge Earthworks</div>
  <nav class="nav"><b>Home</b><em>|</em><span>About Us</span><em>|</em><span>Projects</span><em>|</em><span>Contact Us</span></nav>
  <div class="btn" style="left:995px;top:22px;width:130px;height:37px">Get a Quote</div>
</header>

<!-- hero -->
<section class="hero" role="img" aria-label="Orange excavator digging earth at sunset under a dramatic cloudy sky"></section>
<div class="hero-side">
  <i class="abs" style="left:35px;top:163px;width:1px;height:70px;background:#555"></i>
  <i class="abs soc" style="left:30px;top:256px;width:11px;height:11px;background:#777"></i>
  <i class="abs soc" style="left:30px;top:284px;width:11px;height:11px;background:#777"></i>
  <i class="abs soc" style="left:30px;top:312px;width:11px;height:11px;background:#777"></i>
  <i class="abs soc" style="left:30px;top:340px;width:11px;height:11px;background:#777"></i>
  <i class="abs" style="left:35px;top:385px;width:1px;height:70px;background:#555"></i>
</div>
<h1 class="display" style="position:absolute;left:77px;top:248px;font-size:72px;color:#fff;line-height:0.98">Raising the<br>ground <span class="outline-lime">building</span><br>the future.</h1>
<p class="abs" style="left:77px;top:470px;color:#fff;font-size:12px">Professional Earthworks &amp; Excavation Services in Perth, Western Australia.</p>
<div class="btn" style="left:77px;top:505px;width:128px;height:38px">Get a Quote</div>
<div class="btn btn-ghost" style="left:214px;top:505px;width:155px;height:38px">View Our Projects</div>
<div class="dots"><i></i><i class="on"></i><i></i></div>

<!-- ticker -->
<div class="ticker"><div>Building better homes for better tomorrow<em>✶</em>Building better homes for better tomorrow<em>✶</em>Building better homes for better tomorrow<em>✶</em>Building better homes for better tomorrow<em>✶</em>Building better homes for better tomorrow</div></div>

<!-- what we do -->
<div class="photo" role="img" aria-label="Concrete beam hanging from yellow lifting straps" style="left:908px;top:770px;width:147px;height:181px;background:linear-gradient(180deg,#f4f4e8 0%,#e6e9c2 60%,#d9d9d9 100%)"></div>
<div class="label abs" style="left:75px;top:876px">What we do</div>
<h2 class="display abs" style="left:75px;top:904px;font-size:42px">Reliable earthworks you can trust</h2>
<div class="photo" role="img" aria-label="Yellow excavator working on a cleared site beside tall green trees" style="left:75px;top:994px;width:534px;height:334px;background:linear-gradient(180deg,#3f6e2c 0%,#6f8f3c 45%,#b59a52 75%,#6b5a3e 100%)"></div>
<div class="abs body-copy" style="left:655px;top:1020px;width:400px">
  <p style="margin-bottom:13px">Bluegum Ridge Earthworks delivers high-quality excavation and earthmoving services across Perth and surrounding areas, providing dependable groundwork solutions for residential, commercial, and civil projects. We work closely with builders, developers, and private clients to ensure every site is prepared efficiently, safely, and in full compliance with industry standards.</p>
  <p>With modern, well-maintained machinery, experienced operators, and a strong commitment to accuracy and safety, we focus on delivering results you can rely on. From initial ground preparation to final leveling, we make sure your project starts on solid ground and stays on track from day one.</p>
</div>
<div class="btn" style="left:655px;top:1259px;width:131px;height:39px">Read More</div>

<div class="outline-band"><div>ject construction<i></i>project construction<i></i>project construction<i></i>project construction</div></div>

<!-- services -->
<section class="services">
  <i class="vline" style="left:187px"></i><i class="vline" style="left:375px"></i><i class="vline" style="left:562px"></i><i class="vline" style="left:750px"></i><i class="vline" style="left:937px"></i>
  <h2 class="display abs" style="left:75px;top:100px;font-size:44px;color:#fff">Our earthworks &amp; <span style="color:var(--lime)">excavation services</span></h2>
  <div class="btn" style="left:994px;top:97px;width:131px;height:38px">View More</div>
  <div class="arrow-btn" style="left:75px;top:396px;background:#fff"><svg width="16" height="12" viewBox="0 0 16 12"><path d="M15 6H2M6 1L1 6l5 5" stroke="#111" stroke-width="1.5" fill="none"/></svg></div>
  <div class="arrow-btn" style="left:126px;top:396px;background:var(--lime)"><svg width="16" height="12" viewBox="0 0 16 12"><path d="M1 6h13M10 1l5 5-5 5" stroke="#111" stroke-width="1.5" fill="none"/></svg></div>
</section>
<div class="card" role="img" aria-label="Surveyor in safety vest and hard hat using a tripod level on site" style="left:270px;background:linear-gradient(180deg,#cdd3d6 0%,#b6a892 50%,#8c857a 100%)"><h3>Site preparation &amp; leveling</h3></div>
<div class="card" role="img" aria-label="Excavator silhouetted against an orange sunset" style="left:628px;background:linear-gradient(180deg,#e58a24 0%,#c95e14 50%,#3a2410 100%)">
  <div class="abs" style="left:30px;top:22px;width:43px;height:38px;background:var(--lime);display:flex;align-items:center;justify-content:center"><svg width="13" height="13" viewBox="0 0 13 13"><path d="M2 11L11 2M4 2h7v7" stroke="#111" stroke-width="1.5" fill="none"/></svg></div>
  <h3>Excavation &amp; earthmoving</h3></div>
<div class="card" role="img" aria-label="Excavator bucket digging a trench" style="left:984px;width:216px;background:linear-gradient(180deg,#9a8f82 0%,#6e6052 55%,#3d3127 100%)"><h3>Trenching &amp; drainage</h3></div>

<!-- why choose us -->
<div class="photo" role="img" aria-label="Worker standing beside a trench while an excavator digs" style="left:89px;top:2279px;width:314px;height:348px;background:linear-gradient(180deg,#e8eef2 0%,#b9a88e 55%,#6a4f36 100%)"></div>
<div class="label abs" style="left:451px;top:2296px">Why choose us</div>
<h2 class="display abs" style="left:451px;top:2330px;font-size:44px;line-height:1.12">Built on experience. Driven by<br>reliability.</h2>
<p class="abs body-copy" style="left:451px;top:2434px;width:545px;font-size:11.5px">At Bluegum Ridge Earthworks, we understand that strong groundwork is the foundation of every successful project. That’s why we focus on delivering dependable earthworks solutions backed by experience, modern equipment, and a hands-on approach from start to finish.</p>
<h4 class="display abs" style="left:451px;top:2541px;font-size:19px;font-weight:700">Why clients choose us:</h4>
<ul class="ticks abs" style="left:451px;top:2577px">
  <li>Experienced local operators.</li>
  <li>Modern, well-maintained machinery.</li>
  <li>Reliable timelines &amp; clear communication.</li>
  <li>Safety-focused approach.</li>
  <li>Quality workmanship, every project.</li>
</ul>
<div class="btn" style="left:451px;top:2704px;width:131px;height:37px">Learn More</div>
<div class="photo" role="img" aria-label="Compact excavator with breaker attachment beside a brick building" style="left:725px;top:2520px;width:386px;height:262px;background:linear-gradient(180deg,#e9eef1 0%,#c8b79a 55%,#8a6d4c 100%)"></div>

<!-- projects -->
<div class="label abs" style="left:0;top:2894px;width:1200px;text-align:center">Featured projects</div>
<h2 class="display abs" style="left:0;top:2928px;width:1200px;text-align:center;font-size:44px">Our recent projects</h2>
<div class="arrow-btn" style="left:988px;top:2929px;width:41px;background:var(--ink)"><svg width="16" height="12" viewBox="0 0 16 12"><path d="M15 6H2M6 1L1 6l5 5" stroke="#fff" stroke-width="1.5" fill="none"/></svg></div>
<div class="arrow-btn" style="left:1039px;top:2929px;width:43px;background:var(--lime)"><svg width="16" height="12" viewBox="0 0 16 12"><path d="M1 6h13M10 1l5 5-5 5" stroke="#111" stroke-width="1.5" fill="none"/></svg></div>

<div class="tile" role="img" aria-label="Site supervisor in hard hat holding plans" style="left:123px;top:3003px;background:linear-gradient(180deg,#b9c2c8 0%,#c9b15a 55%,#5d5a4e 100%)"></div>
<div class="tile" role="img" aria-label="Backhoe loader working on a dirt site" style="left:366px;top:3003px;background:linear-gradient(180deg,#7f8c96 0%,#8e7c5c 55%,#3b3128 100%)">
  <div class="abs" style="left:96px;top:79px;width:38px;height:38px;background:var(--lime);display:flex;align-items:center;justify-content:center"><svg width="14" height="14" viewBox="0 0 24 24"><path d="M10 14a5 5 0 0 0 7 0l3-3a5 5 0 0 0-7-7l-1 1M14 10a5 5 0 0 0-7 0l-3 3a5 5 0 0 0 7 7l1-1" stroke="#111" stroke-width="2.2" fill="none"/></svg></div>
</div>
<div class="tile" role="img" aria-label="Forestry mulcher clearing land among trees" style="left:609px;top:3003px;background:linear-gradient(180deg,#5f7a4a 0%,#8b7a4e 55%,#5c4a35 100%)"></div>
<div class="tile" role="img" aria-label="Excavator bucket lifting red earth under blue sky" style="left:852px;top:3003px;background:linear-gradient(180deg,#5d93c8 0%,#c58a3c 50%,#a65c2c 100%)"></div>
<div class="tile" role="img" aria-label="Excavator silhouette at sunset" style="left:123px;top:3209px;background:linear-gradient(180deg,#f0b26a 0%,#d87b3a 55%,#6b4a36 100%)"></div>
<div class="tile" role="img" aria-label="Excavator digging a muddy site" style="left:366px;top:3209px;background:linear-gradient(180deg,#6f9cc6 0%,#b99a6c 55%,#6d4a34 100%)"></div>
<div class="tile" role="img" aria-label="Wheel loader moving sand in front of a crane" style="left:609px;top:3209px;background:linear-gradient(180deg,#a7c4dc 0%,#cf9c55 55%,#8d5f30 100%)"></div>
<div class="tile" role="img" aria-label="Engineer in hard hat using a laptop on site" style="left:852px;top:3209px;background:linear-gradient(180deg,#b8bfc6 0%,#9aa3a9 50%,#4e5a66 100%)"></div>
<div class="btn" style="left:521px;top:3434px;width:158px;height:38px">View More Projects</div>

<!-- cta -->
<section class="cta">
  <h2 class="display abs" style="left:75px;top:55px;font-size:46px">Ready to get started?</h2>
  <p class="abs" style="left:527px;top:52px;width:410px;font-size:11.5px;line-height:1.55;color:#333">Whether you’re planning a new build or need professional excavation services, Bluegum Ridge Earthworks is here to help. Get in touch today for a fast, reliable quote.</p>
  <div class="btn" style="left:995px;top:56px;width:130px;height:37px;background:#fff">Contact Us</div>
</section>

<!-- footer -->
<footer class="footer">
  <div class="abs" style="left:75px;top:120px;display:flex;align-items:center;gap:10px;font-weight:700;font-size:17px"><i style="display:block;width:24px;height:24px;background:var(--lime)"></i>Bluegum Ridge<br>Earthworks</div>

  <div class="foot-h" style="left:364px">Quick links</div>
  <ul class="foot-list" style="left:364px;top:107px"><li>Home</li><li>About</li><li>Projects</li><li>Contact Us</li></ul>

  <div class="foot-h" style="left:591px">Contact us</div>
  <ul class="foot-list" style="left:591px;top:118px;line-height:16px">
    <li style="margin-bottom:16px"><svg width="10" height="10" viewBox="0 0 24 24" style="margin-top:3px"><path fill="#d4dc00" d="M6.6 10.8a15 15 0 0 0 6.6 6.6l2.2-2.2a1 1 0 0 1 1-.25 11.4 11.4 0 0 0 3.6.57 1 1 0 0 1 1 1V20a1 1 0 0 1-1 1A17 17 0 0 1 3 4a1 1 0 0 1 1-1h3.5a1 1 0 0 1 1 1c0 1.25.2 2.45.57 3.57a1 1 0 0 1-.25 1z"/></svg>123 ( 456 ) 7890</li>
    <li style="margin-bottom:16px"><svg width="11" height="9" viewBox="0 0 24 18" style="margin-top:4px"><rect width="24" height="18" rx="2" fill="#d4dc00"/><path d="M1 2l11 8 11-8" stroke="#0d0d0d" stroke-width="2" fill="none"/></svg><u>info@bluegumridgeearthworks.com.au</u></li>
    <li><svg width="9" height="11" viewBox="0 0 18 24" style="margin-top:3px"><path fill="#d4dc00" d="M9 0a9 9 0 0 0-9 9c0 6.8 9 15 9 15s9-8.2 9-15a9 9 0 0 0-9-9zm0 12.5A3.5 3.5 0 1 1 9 5.5a3.5 3.5 0 0 1 0 7z"/></svg>Perth, Western Australia<br>(Servicing Perth &amp; Surrounding Areas)</li>
  </ul>

  <div class="foot-h" style="left:887px">Subscribe newsletter</div>
  <p class="abs" style="left:897px;top:112px;width:200px;font-size:11px;line-height:1.35">Subscribe newsletter for the latest offers and news</p>
  <div class="abs" style="left:887px;top:157px;width:198px;height:33px;background:#fff;font-size:9px;color:#999;padding:11px 14px">Enter Email...</div>
  <div class="abs" style="left:1085px;top:157px;width:40px;height:33px;background:var(--lime);display:flex;align-items:center;justify-content:center"><svg width="16" height="10" viewBox="0 0 16 10"><path d="M1 5h13M10 1l4 4-4 4" stroke="#111" stroke-width="1.4" fill="none"/></svg></div>
  <div class="abs" style="left:897px;top:214px;display:flex;gap:7px"><i class="soc" style="background:var(--lime)"></i><i class="soc"></i><i class="soc"></i><i class="soc"></i></div>

  <i class="abs" style="left:75px;top:310px;width:1050px;height:1px;background:#444"></i>
  <div class="abs" style="left:1144px;top:280px;width:34px;height:35px;background:var(--lime);display:flex;align-items:center;justify-content:center"><svg width="10" height="14" viewBox="0 0 10 14"><path d="M5 13V2M1 6l4-4 4 4" stroke="#111" stroke-width="1.4" fill="none"/></svg></div>
  <p class="abs" style="left:0;top:334px;width:1200px;text-align:center;font-size:11px">© 2026 Bluegum Ridge Earthworks. All Rights Reserved.</p>
</footer>

</body>
</html>
```